Looking for a modern, Professional business card design

We have a simple business card, but are looking for a more modern, professional look. A sample of the basic card is attached as well as the logo. We would also like to add that we offer:
Struggling with your finances?
- Learn to become debt free
- Discover the power of cash
- Control your money instead of it controlling you
Let us help you achieve a new level of financial freedom!
Also, we would like to have a "SPECIAL OFFER!: FREE 30 minute consultation"
Financial Planning

```html
<!DOCTYPE html>
<html lang="en">
<head>
<meta charset="utf-8">
<title>Harbor Money Coaching – Business Card</title>
<link rel="stylesheet" href="https://fonts.googleapis.com/css2?family=Arimo:wght@400;700&display=swap">
<style>
  :root {
    --backdrop: #3a3b3d;
    --card-white: #ffffff;
    --card-black: #0d0d0d;
    --green: #6cb33f;
    --green-light: #a6d66f;
    --ink: #2b2b2b;
    --ink-soft: #444444;
    --on-dark: #e8e8e8;
  }
  * { box-sizing: border-box; margin: 0; padding: 0; }
  html, body {
    width: 1200px; height: 950px; overflow: hidden;
    background: var(--backdrop);
    font-family: "Arimo", Arial, sans-serif;
  }
  .sheet {
    position: relative; width: 1200px; height: 950px;
    display: flex; flex-direction: column; align-items: center; justify-content: center; gap: 40px;
  }
  .card {
    position: relative; width: 735px; height: 420px; overflow: hidden;
    box-shadow: 0 10px 30px rgba(0,0,0,.45);
  }
  /* Back */
  .card--back {
    background: linear-gradient(160deg, #2a2a2a 0%, var(--card-black) 45%, #000 100%);
    color: var(--on-dark);
    text-align: center;
    padding: 70px 50px 0;
  }
  .brand {
    display: inline-flex; align-items: center; gap: 14px;
    font-weight: 700; letter-spacing: .5px;
  }
  .brand__dot { width: 26px; height: 26px; border-radius: 50%; background: var(--green); flex: none; }
  .card--back .brand { font-size: 40px; color: #f2f2f2; }
  .pitch { margin-top: 46px; }
  .pitch__heading { font-size: 24px; font-weight: 700; letter-spacing: .5px; }
  .pitch__list { list-style: none; margin-top: 14px; font-size: 19px; line-height: 1.5; }
  .pitch__list li::before { content: "•"; color: var(--green); margin-right: 10px; }
  .pitch__close { margin-top: 12px; font-size: 19px; }
  .offer { margin-top: 22px; font-size: 22px; font-weight: 700; }
  .offer span { color: var(--green); }

  /* Front */
  .card--front { background: var(--card-white); }
  .front__mark { position: absolute; left: -120px; top: -40px; }
  .front__info {
    position: absolute; right: 52px; top: 46px; width: 400px;
    text-align: right;
  }
  .person__name { font-size: 27px; color: var(--green); }
  .person__role { font-size: 21px; color: var(--ink); margin-top: 4px; }
  .card--front .brand { margin-top: 56px; font-size: 34px; color: var(--ink); }
  .contact { margin-top: 54px; font-size: 21px; line-height: 1.45; color: var(--ink-soft); }
  .contact__label { color: var(--green); font-weight: 700; }
</style>
</head>
<body>
<main class="sheet">

  <section class="card card--back" aria-label="Card back">
    <div class="brand"><span class="brand__dot"></span>Harbor Money Coaching</div>
    <div class="pitch">
      <p class="pitch__heading">STRUGGLING WITH YOUR FINANCES?</p>
      <ul class="pitch__list">
        <li>Learn to become debt free</li>
        <li>Discover the power of cash</li>
        <li>Control your money instead of it controlling you</li>
      </ul>
      <p class="pitch__close">Achieve a new level of financial freedom!</p>
      <p class="offer"><span>SPECIAL OFFER!</span> FREE 30 minute consultation</p>
    </div>
  </section>

  <section class="card card--front" aria-label="Card front">
    <svg class="front__mark" width="420" height="500" viewBox="0 0 420 500" aria-hidden="true">
      <defs>
        <radialGradient id="markGlow" cx="50%" cy="50%" r="50%">
          <stop offset="0" stop-color="#a6d66f" stop-opacity=".55"/>
          <stop offset="1" stop-color="#6cb33f" stop-opacity=".15"/>
        </radialGradient>
      </defs>
      <circle cx="210" cy="250" r="200" fill="url(#markGlow)"/>
    </svg>
    <div class="front__info">
      <p class="person__name">Daniel R. Hayes</p>
      <p class="person__role">Personal Financial Coach</p>
      <div class="brand"><span class="brand__dot"></span>Harbor Money Coaching</div>
      <div class="contact">
        <p><span class="contact__label">Mob:</span> (555) 014-2290</p>
        <p>daniel@steadymoneypath.com</p>
        <p>www.steadymoneypath.com</p>
      </div>
    </div>
  </section>

</main>
</body>
</html>
```